Upscale business cards needed for Board of Directors

We need professional business cards created for members of our family business Board of Directors. We would like these relatively simple and straightforward, but also with a unique element to set them apart. Probably stick with neutral and simple colors - white, grey etc. We need space for the traditional elements, including name, title, address, email/phone number. And we will be creating several from this template so it needs to be template that is easy to switch information in and out of.
Business
See description

```html
<!DOCTYPE html>
<html lang="en">
<head>
<meta charset="utf-8">
<title>Harbourline Holdings – Business Cards</title>
<link href="https://fonts.googleapis.com/css2?family=Lato:wght@400;700;900&display=swap" rel="stylesheet">
<style>
  :root {
    --ink: #0b0b0b;
    --paper: #ffffff;
    --gold: #b19e73;
    --stage: #2e2e2e;
    --font: 'Lato', sans-serif;
  }
  * { margin: 0; padding: 0; box-sizing: border-box; }
  html, body { width: 1200px; height: 900px; overflow: hidden; }
  body { background: var(--stage); font-family: var(--font); position: relative; }

  .card {
    position: absolute;
    width: 560px;
    height: 320px;
    overflow: hidden;
    box-shadow: 0 10px 30px rgba(0,0,0,.45);
  }
  .card-back { left: 560px; top: 90px; background: var(--ink); }
  .card-front { left: 80px; top: 480px; background: var(--paper); }

  .wordmark {
    font-family: var(--font);
    font-weight: 900;
    text-transform: uppercase;
    line-height: 1.05;
    letter-spacing: 2px;
  }
  .card-back .wordmark {
    position: absolute; left: 0; right: 0; top: 92px;
    text-align: center; color: var(--paper); font-size: 40px;
  }
  .card-back .web {
    position: absolute; left: 0; right: 0; top: 250px;
    text-align: center; color: var(--paper);
    font-size: 15px; letter-spacing: 2px;
  }

  .front-art { position: absolute; inset: 0; }
  .card-front .wordmark {
    position: absolute; left: 36px; top: 22px;
    color: var(--ink); font-size: 32px;
  }
  .person { position: absolute; left: 36px; top: 94px; }
  .person-name { color: var(--gold); font-size: 20px; font-weight: 400; line-height: 24px; }
  .person-title { color: var(--ink); font-size: 12px; line-height: 15px; }

  .contact {
    position: absolute; left: 330px; top: 214px;
    color: var(--paper); font-size: 13px; line-height: 15px;
  }
  .contact-address { margin-bottom: 4px; }
  .contact-row { display: flex; align-items: center; gap: 9px; }
  .contact-row svg { width: 11px; height: 11px; flex: none; }
</style>
</head>
<body>

<section class="card card-back" aria-label="Card back">
  <div class="wordmark">Harbourline<br>Holdings</div>
  <div class="web">www.harbourline.com</div>
</section>

<section class="card card-front" aria-label="Card front">
  <svg class="front-art" viewBox="0 0 560 320" width="560" height="320" aria-hidden="true">
    <path d="M0,142 C150,162 300,172 420,168 C480,166 530,157 560,150 L560,164 C530,172 480,180 420,182 C300,186 150,178 0,156 Z" fill="var(--gold)"/>
    <path d="M0,164 C150,186 300,194 420,190 C480,188 530,180 560,172 L560,178 C530,186 480,194 420,196 C300,200 150,194 0,172 Z" fill="var(--ink)"/>
    <path d="M0,180 C150,200 300,206 420,202 C480,200 530,192 560,184 L560,320 L0,320 Z" fill="var(--ink)"/>
  </svg>

  <div class="wordmark">Harbourline<br>Holdings</div>

  <div class="person">
    <div class="person-name">Mark Ellison</div>
    <div class="person-title">Director</div>
  </div>

  <div class="contact">
    <div class="contact-address">1450 Cedar Row<br>Millbrook TX 78010</div>
    <div class="contact-row">
      <svg viewBox="0 0 12 12"><path d="M2.5 1 L4.5 1 L5.2 3.5 L4 4.5 C4.6 6 6 7.4 7.5 8 L8.5 6.8 L11 7.5 L11 9.5 C11 10.4 10.2 11 9.3 11 C4.6 10.6 1.4 7.4 1 2.7 C1 1.8 1.6 1 2.5 1 Z" fill="var(--gold)"/></svg>
      <span>555 010 4400</span>
    </div>
    <div class="contact-row">
      <svg viewBox="0 0 12 12"><rect x="3" y="1" width="6" height="3" fill="var(--gold)"/><rect x="1" y="4.5" width="10" height="4.5" rx="1" fill="var(--gold)"/><rect x="3" y="7.5" width="6" height="3.5" fill="var(--gold)"/></svg>
      <span>555 010 4401</span>
    </div>
    <div class="contact-row">
      <svg viewBox="0 0 12 12"><rect x="1" y="2.5" width="10" height="7" fill="var(--gold)"/><path d="M1 2.5 L6 6.5 L11 2.5" stroke="var(--ink)" stroke-width="1" fill="none"/></svg>
      <span>info@harbourline.com</span>
    </div>
    <div class="contact-row">
      <svg viewBox="0 0 12 12"><circle cx="6" cy="6" r="5" fill="var(--gold)"/><path d="M1 6 H11 M6 1 C3.5 3.5 3.5 8.5 6 11 M6 1 C8.5 3.5 8.5 8.5 6 11" stroke="var(--ink)" stroke-width=".8" fill="none"/></svg>
      <span>www.harbourline.com</span>
    </div>
  </div>
</section>

</body>
</html>
```